Moxy Fen needs some awesome stationary

Do you have what it takes to get my brand? You either do or you don't, have a crack at a design and you my just win my business.

I don't want to waste your or my time, so put your creative genius on either a business card or envelope.

I however need a package of stationary that follows the same brand. I will message you to complete the remaining should I like your first submission.

Here is what I need, have a go!

Basically I need the following for my small business based in melbourne.
- Letterhead (printer ready and MS Word)
- Business Card
- Compliments Slip
- Envelope
- Proposal Cover Page (MS Word only)
- Presentation Folder
- Marbled Fox Cards
- Student Name Tent
- Index Cards
- Vell-Ka

I am establishing the brand and it must be modern, professional but also relaxed; that is not formal and not corporate. It represents a company are leaders, but small enough to care and operate like a bunch of friends. We are bringing people and conversations back to business, and turfing out all the bureaucracy and crazy and wasteful procedures. Its about "lets talk and figure it out together and find even better ways".

Target Market(s)

Mainly companies that build software products, but Agile practices are used in many other industries (even graphic design projects)

Industry/Entity Type

Information Technology

Font styles to use
Sans Serif

Colors
3176b5
aaaaaa

Requirements
Must have
• I like curves and circles and not boxes or rectangles.
• I want a colour rich design with my brand colours, but it must be balanced.
• I want more modern than traditional, but simple modern
Should not have
• Not corporate
• Please don't waste my time if your not going to think about it.
• Don't mess with my primary logo
• Don't change my colours
• Don't overlay logo on image

```html
<!DOCTYPE html>
<html lang="en">
<head>
<meta charset="utf-8">
<title>Moxy Fen – Business Card</title>
<link href="https://fonts.googleapis.com/css2?family=Open+Sans:wght@400;600;700&display=swap" rel="stylesheet">
<style>
  :root {
    --brand-blue: #2b5aa0;
    --brand-grey: #959eae;
    --text-dark: #3d3d3d;
    --text-grey: #8a8f99;
    --card-white: #ffffff;
    --backdrop: #dcdcdc;
  }
  * { margin: 0; padding: 0; box-sizing: border-box; }
  html, body {
    width: 1200px; height: 987px; overflow: hidden;
    background: var(--backdrop);
    font-family: "Open Sans", Arial, sans-serif;
  }
  .canvas { position: relative; width: 1200px; height: 987px; }
  .card {
    position: absolute; top: 337px; width: 503px; height: 288px;
    background: var(--card-white); border-radius: 16px; overflow: hidden;
  }
  .card--front { left: 89px; }
  .card--back { left: 606px; }

  .accent-circle { position: absolute; border-radius: 50%; }
  .card--front .accent-circle {
    width: 300px; height: 300px; left: 296px; top: -6px;
    background: var(--brand-blue);
  }
  .card--back .accent-circle {
    width: 300px; height: 300px; left: -50px; top: -6px;
    background: var(--brand-grey);
  }

  .contact { position: absolute; left: 26px; top: 52px; color: var(--text-dark); }
  .contact__name { font-size: 19px; font-weight: 600; color: var(--brand-blue); line-height: 22px; }
  .contact__role { font-size: 14px; color: var(--text-grey); line-height: 19px; }
  .contact__line { font-size: 14px; line-height: 18px; }
  .divider { width: 20px; height: 2px; background: var(--brand-blue); margin: 8px 0 10px; }
  .contact__row { display: flex; align-items: center; gap: 7px; font-size: 14px; line-height: 20px; }
  .contact__row svg { width: 13px; height: 13px; fill: var(--brand-blue); flex: none; }

  .brand {
    position: absolute; right: 54px; top: 92px;
    display: flex; flex-direction: column; align-items: center; gap: 12px;
  }
  .brand__dot { width: 58px; height: 58px; border-radius: 50%; background: var(--brand-blue); }
  .brand__name { font-size: 30px; font-weight: 700; color: var(--brand-blue); line-height: 1; }
</style>
</head>
<body>
<div class="canvas">
  <section class="card card--front">
    <div class="accent-circle"></div>
    <div class="contact">
      <p class="contact__name">Dara Quill</p>
      <p class="contact__role">CEO, Professional Scrum Trainer</p>
      <p class="contact__line">dara@moxyfen.com.au</p>
      <div class="divider"></div>
      <p class="contact__line">PO Box 4417</p>
      <p class="contact__line">Ashbury Vale</p>
      <p class="contact__line">VIC 3190, Australia</p>
      <div class="divider"></div>
      <p class="contact__row">
        <svg viewBox="0 0 24 24"><path d="M6.6 10.8a15.1 15.1 0 0 0 6.6 6.6l2.2-2.2a1 1 0 0 1 1-.25 11.4 11.4 0 0 0 3.6.57 1 1 0 0 1 1 1V20a1 1 0 0 1-1 1A17 17 0 0 1 3 4a1 1 0 0 1 1-1h3.5a1 1 0 0 1 1 1c0 1.25.2 2.45.57 3.57a1 1 0 0 1-.25 1z"/></svg>
        1300MOXYF
      </p>
      <p class="contact__row">
        <svg viewBox="0 0 24 24"><path d="M7 1h10a2 2 0 0 1 2 2v18a2 2 0 0 1-2 2H7a2 2 0 0 1-2-2V3a2 2 0 0 1 2-2zm0 3v14h10V4zm5 15.5a1.2 1.2 0 1 0 0 2.4 1.2 1.2 0 0 0 0-2.4z"/></svg>
        +61 400 123 987
      </p>
      <p class="contact__row">
        <svg viewBox="0 0 24 24"><circle cx="12" cy="12" r="10"/><path d="M2 12h20M12 2c3 3 3 17 0 20M12 2c-3 3-3 17 0 20" stroke="#fff" stroke-width="1.5" fill="none"/></svg>
        www.moxyfen.com.au
      </p>
    </div>
  </section>

  <section class="card card--back">
    <div class="accent-circle"></div>
    <div class="brand">
      <div class="brand__dot"></div>
      <p class="brand__name">Moxy Fen</p>
    </div>
  </section>
</div>
</body>
</html>
```